New website for a business that provides behaviour analysis

A new website that details the services that are provided around behaviour analysis for people with a disability through QPKV. There also needs to incorporate an about us and a staff page, Plus a referral form that is a google doc.
The business already has a web address that needs to be tailored.
Soft colours are preferred.
Do not have lots of pictures, keep them minimal.
A logo for the business is also needed to be incorporated, and this is a separate project that can be awarded to the website winner.
Website needs to be able to be used on WIX who will be the host for the design.

Target Market(s)

QPKV clients requiring behaviour support clician

Industry/Entity Type

Clinical behaviour support and analysis

Colors
00AB8E
00BBA5
67D7C9
C6EFE9
E9F9F6

Requirements
Must have
• Soft colours, preferable pale turquoise, minimal pictures, clean, sophisticated and classical look

```html
<!DOCTYPE html>
<html lang="en">
<head>
<meta charset="utf-8">
<title>Calmwell — Free Checkup</title>
<link rel="stylesheet" href="https://fonts.googleapis.com/css2?family=Playfair+Display:wght@700;800&family=Work+Sans:wght@400;500;600;700&display=swap">
<style>
:root{
  --teal:#00AB8E;
  --teal-2:#00BBA5;
  --teal-3:#67D7C9;
  --mint:#C6EFE9;
  --mist:#E9F9F6;
  --ink:#1d1d1d;
  --page:#FDFEFE;
  --white:#ffffff;
}
*{box-sizing:border-box;margin:0;padding:0}
html,body{width:1200px;height:2680px;overflow:hidden}
body{background:var(--page);font-family:"Work Sans",sans-serif;color:var(--ink);position:relative}
.serif{font-family:"Playfair Display",serif}
.abs{position:absolute}
svg{display:block}

/* top bar */
.topbar{left:0;top:0;width:1200px;height:70px;background:var(--white)}
.brand{left:164px;top:16px;font-family:"Playfair Display",serif;font-weight:800;font-size:32px;color:var(--teal);letter-spacing:.5px}
.info{top:17px;display:flex;gap:8px;align-items:flex-start;color:var(--teal);font-size:13.5px;line-height:19px;font-weight:500}
.info b{display:block;font-weight:500;letter-spacing:.5px}

/* nav */
.nav{left:0;top:70px;width:1200px;height:70px;background:var(--teal)}
.nav ul{position:absolute;left:164px;top:24px;display:flex;gap:19px;list-style:none;color:var(--white);font-size:15.5px}
.nav li.active{font-weight:700}
.search{position:absolute;left:838px;top:24px}
.btn-appoint{position:absolute;left:884px;top:15px;width:152px;height:39px;border-radius:20px;background:var(--mist);color:var(--teal);font-size:14px;font-weight:500;display:flex;align-items:center;justify-content:center}

/* hero */
.hero{left:0;top:140px;width:1200px;height:215px;background:linear-gradient(90deg,#cfd6d3 0%,#e7ebea 35%,#f1f3f3 60%,#e4e9ea 100%);overflow:hidden}
.hero-shade{left:0;top:0;width:1200px;height:215px;background:linear-gradient(90deg,rgba(255,255,255,.55),rgba(255,255,255,.15))}
.hero-deco{left:-110px;top:-120px;width:214px;height:214px;border-radius:50%;background:rgba(103,215,201,.75)}
.crumb{left:164px;top:68px;font-size:15.5px;color:var(--teal-2)}
.hero h1{left:164px;top:82px;font-family:"Playfair Display",serif;font-weight:800;font-size:45px;color:var(--teal-2)}
.hero-bar{left:0;top:355px;width:1200px;height:6px;background:var(--mist)}
.hero-bar i{position:absolute;left:268px;top:0;width:932px;height:6px;background:var(--teal-2)}

/* service sidebar */
.sidebar{left:164px;top:413px;width:211px;height:425px;border:1px solid var(--mint);background:var(--white)}
.svc{height:70px;display:flex;align-items:center;gap:10px;padding-left:28px;font-size:14.5px;color:var(--ink)}
.svc.active{background:var(--teal);color:var(--white)}
.svc svg{flex:none}

/* main */
.main-photo{left:393px;top:413px;width:643px;height:399px;background:linear-gradient(100deg,#7c7f6e 0%,#d9dcdc 35%,#f0f2f3 55%,#bfc5c8 75%,#e6e9ea 100%)}
.main h2{position:absolute;left:393px;top:835px;font-family:"Playfair Display",serif;font-weight:700;font-size:30px;color:var(--teal);letter-spacing:.3px}
.points{left:393px;top:893px;display:grid;grid-template-columns:222px 158px 220px;row-gap:14px;font-size:16.5px}
.points span{display:flex;align-items:center;gap:10px}
.points span::before{content:"";width:13px;height:13px;border-radius:50%;background:var(--teal-2)}
.copy{left:393px;top:971px;width:645px;font-size:14px;line-height:19.5px}
.copy p+p{margin-top:7px}

/* section titles */
.kicker{width:1200px;left:0;text-align:center;font-weight:700;font-size:15.5px;letter-spacing:3px;color:var(--teal-2)}
.title{width:1200px;left:0;text-align:center;font-family:"Playfair Display",serif;font-weight:700;font-size:31px;color:var(--teal)}

/* team */
.card{top:1301px;width:278px;height:473px;background:var(--mist)}
.card .photo{height:307px}
.card .name{margin-top:24px;text-align:center;color:var(--teal);font-size:15.5px}
.card .dept{margin-top:9px;text-align:center;color:var(--teal);font-weight:700;font-size:15.5px;letter-spacing:3px}
.card .social{display:flex;gap:18px;justify-content:center;margin-top:13px}
.dot-btn{width:21px;height:21px;border-radius:50%;background:var(--teal)}
.card .view{position:absolute;left:0;bottom:0;width:278px;height:41px;background:var(--teal);color:var(--white);font-size:14.5px;display:flex;align-items:center;justify-content:center}
.pager{left:567px;top:1803px;display:flex;gap:9px;align-items:center}
.pager i{width:14px;height:14px;border-radius:50%;background:var(--mist)}
.pager i.on{width:16px;height:16px;background:var(--teal)}

/* contact */
.cbox{top:2045px;width:205px;height:205px;background:var(--mist);padding:46px 0 0 26px;color:var(--teal-2)}
.cbox.hl{background:var(--teal);color:var(--white)}
.cbox h3{margin-top:18px;font-size:15.5px;font-weight:700;color:var(--teal)}
.cbox.hl h3{color:var(--white)}
.cbox p{font-size:14px;line-height:24px}
.cbox p.sm{font-size:12px}

/* footer */
.footer{left:0;top:2306px;width:1200px;height:374px;background:var(--teal);color:var(--white)}
.footer .fbrand{position:absolute;left:164px;top:60px;font-family:"Playfair Display",serif;font-weight:800;font-size:32px}
.footer .tag{position:absolute;left:164px;top:118px;font-size:16px;line-height:22px}
.fcol{position:absolute;top:65px}
.fcol h4{font-size:15.5px;font-weight:700}
.fcol ul{list-style:none;margin-top:32px;font-size:14.5px;line-height:25.5px}
.news{position:absolute;left:796px;top:115px;width:239px;height:44px;background:var(--mist);border-radius:3px;display:flex;align-items:center;justify-content:space-between;padding:0 14px 0 9px;color:var(--teal);font-size:14.5px}
.rule{position:absolute;left:164px;top:250px;width:872px;height:1px;background:rgba(255,255,255,.7)}
.copyright{position:absolute;left:164px;top:297px;font-size:14px}
.fsocial{position:absolute;left:937px;top:295px;display:flex;gap:18px}
.fsocial i{width:21px;height:21px;border-radius:50%;background:var(--white)}
</style>
</head>
<body>

<header class="abs topbar">
  <div class="abs brand">CALMWELL</div>
  <div class="abs info" style="left:490px">
    <svg width="32" height="32" viewBox="0 0 32 32" fill="none" stroke="var(--teal)" stroke-width="1.6"><path d="M8 6l4 5-2 3c1.5 3 4 5.5 7 7l3-2 5 4-2 4c-9 0-19-10-19-19z"/><path d="M19 8a6 6 0 0 1 5 5M19 4a10 10 0 0 1 9 9"/></svg>
    <div><b>EMERGENCY</b>(555) 010-2040</div>
  </div>
  <div class="abs info" style="left:668px">
    <svg width="30" height="30" viewBox="0 0 30 30" fill="none" stroke="var(--teal)" stroke-width="1.6"><circle cx="15" cy="15" r="12"/><path d="M15 8v8l-4 3"/></svg>
    <div><b>WORK HOUR</b>09:00 - 20:00 Everyday</div>
  </div>
  <div class="abs info" style="left:882px">
    <svg width="30" height="34" viewBox="0 0 30 34" fill="none" stroke="var(--teal)" stroke-width="1.6"><path d="M15 32s-11-11-11-18a11 11 0 0 1 22 0c0 7-11 18-11 18z"/><circle cx="15" cy="14" r="4"/></svg>
    <div><b>LOCATION</b>0123 Some Place</div>
  </div>
</header>

<nav class="abs nav">
  <ul>
    <li>Home</li><li>About us</li><li class="active">Services</li><li>Doctors</li><li>News</li><li>Contact</li>
  </ul>
  <svg class="search" width="22" height="22" viewBox="0 0 22 22" fill="none" stroke="#fff" stroke-width="1.8"><circle cx="10" cy="10" r="8"/><path d="M16 16l5 5"/></svg>
  <div class="btn-appoint">Appointment</div>
</nav>

<section class="abs hero" role="img" aria-label="Clinician greeting a patient in a bright consultation room">
  <div class="abs hero-shade"></div>
  <div class="abs hero-deco"></div>
  <div class="abs crumb">Home / Services</div>
  <h1 class="abs">Free Checkup</h1>
</section>
<div class="abs hero-bar"><i></i></div>

<aside class="abs sidebar">
  <div class="svc active">
    <svg width="26" height="26" viewBox="0 0 26 26" fill="none" stroke="#fff" stroke-width="1.6"><rect x="4" y="4" width="18" height="18" rx="9"/><path d="M6 20L20 6M9 11l2 2M13 9l2 2M11 15l2 2"/></svg>Free Checkup</div>
  <div class="svc">
    <svg width="30" height="28" viewBox="0 0 30 28" fill="none" stroke="var(--teal)" stroke-width="1.8"><path d="M15 25S3 17 3 9a6 6 0 0 1 12-2 6 6 0 0 1 12 2c0 8-12 16-12 16z"/><path d="M6 13h5l2-3 3 6 2-3h6"/></svg>Cardiogram</div>
  <div class="svc">
    <svg width="28" height="28" viewBox="0 0 28 28" fill="none" stroke="var(--teal)" stroke-width="1.8"><rect x="2" y="2" width="24" height="24" rx="2"/><path d="M11 7h6v4h4v6h-4v4h-6v-4H7v-6h4z"/></svg>Dna Testing</div>
  <div class="svc" style="height:80px">
    <svg width="28" height="38" viewBox="0 0 28 38" fill="none" stroke="var(--teal)" stroke-width="1.8"><path d="M9 2h10M14 2v5M5 7h18v22H5zM14 29v7"/><path d="M12 14h4v3h3v4h-3v3h-4v-3H9v-4h3z"/></svg>Blood Bank</div>
  <div class="svc" style="height:80px">
    <svg width="28" height="28" viewBox="0 0 28 28" fill="none" stroke="var(--teal)" stroke-width="1.8"><rect x="2" y="2" width="24" height="24" rx="2"/><path d="M11 7h6v4h4v6h-4v4h-6v-4H7v-6h4z"/></svg>Dermalogy</div>
  <div class="svc">
    <svg width="28" height="28" viewBox="0 0 28 28" fill="none" stroke="var(--teal)" stroke-width="1.8"><rect x="2" y="2" width="24" height="24" rx="2"/><path d="M11 7h6v4h4v6h-4v4h-6v-4H7v-6h4z"/></svg>Orthopedic</div>
</aside>

<section class="main">
  <div class="abs main-photo" role="img" aria-label="Clinician in a white coat checking the wrist of a seated patient"></div>
  <h2>A passion for putting patients first</h2>
  <div class="abs points">
    <span>A Passion for Healing</span><span>5-Star Care</span><span>A Legacy of Excellence</span>
    <span>All our best</span><span>Believe in Us</span><span>Always Caring</span>
  </div>
  <div class="abs copy">
    <p>Lorem ipsum dolor sit amet, consectetur adipiscing elit. Quisque placerat scelerisque tortor ornare ornare. Quisque placerat scelerisque tortor ornare ornare Convallis felis vitae tortor augue. Velit nascetur proin massa in. Consequat faucibus porttitor enim et.</p>
    <p>Lorem ipsum dolor sit amet, consectetur adipiscing elit. Quisque placerat scelerisque. Convallis felis vitae tortor augue. Velit nascetur proin massa in.</p>
  </div>
</section>

<section class="team">
  <div class="abs kicker" style="top:1188px">MEET THE</div>
  <div class="abs title" style="top:1208px">Team Members</div>

  <article class="abs card" style="left:164px">
    <div class="photo" role="img" aria-label="Portrait of a smiling doctor with a stethoscope" style="background:linear-gradient(180deg,#e9e4ea,#d8d6dc)"></div>
    <div class="name">Doctor’s Name</div><div class="dept">NEUROLOGY</div>
    <div class="social"><i class="dot-btn"></i><i class="dot-btn"></i><i class="dot-btn"></i></div>
    <div class="view">View Profile</div>
  </article>
  <article class="abs card" style="left:460px">
    <div class="photo" role="img" aria-label="Portrait of a doctor in a white coat and tie" style="background:linear-gradient(180deg,#eeeeee,#dcdcdc)"></div>
    <div class="name">Doctor’s Name</div><div class="dept">NEUROLOGY</div>
    <div class="social"><i class="dot-btn"></i><i class="dot-btn"></i><i class="dot-btn"></i></div>
    <div class="view">View Profile</div>
  </article>
  <article class="abs card" style="left:757px">
    <div class="photo" role="img" aria-label="Portrait of a doctor in a clinic lobby" style="background:linear-gradient(100deg,#a8a78a,#dfe3df 55%,#c9d0cf)"></div>
    <div class="name">Doctor’s Name</div><div class="dept">NEUROLOGY</div>
    <div class="social"><i class="dot-btn"></i><i class="dot-btn"></i><i class="dot-btn"></i></div>
    <div class="view">View Profile</div>
  </article>

  <div class="abs pager"><i></i><i class="on"></i><i></i></div>
</section>

<section class="contact">
  <div class="abs kicker" style="top:1931px">GET IN TOUCH</div>
  <div class="abs title" style="top:1951px">Contact</div>

  <div class="abs cbox" style="left:164px">
    <svg width="32" height="32" viewBox="0 0 32 32" fill="none" stroke="var(--teal)" stroke-width="1.6"><path d="M8 6l4 5-2 3c1.5 3 4 5.5 7 7l3-2 5 4-2 4c-9 0-19-10-19-19z"/><path d="M19 8a6 6 0 0 1 5 5M19 4a10 10 0 0 1 9 9"/></svg>
    <h3>EMERGENCY</h3><p>(555) 010-2040<br>(555) 010-3050</p>
  </div>
  <div class="abs cbox hl" style="left:386px">
    <svg width="30" height="34" viewBox="0 0 30 34" fill="none" stroke="#fff" stroke-width="1.6"><path d="M15 32s-11-11-11-18a11 11 0 0 1 22 0c0 7-11 18-11 18z"/><circle cx="15" cy="14" r="4"/></svg>
    <h3>LOCATION</h3><p>0123 Some place<br>9876 Some country</p>
  </div>
  <div class="abs cbox" style="left:608px">
    <svg width="34" height="32" viewBox="0 0 34 32" fill="none" stroke="var(--teal)" stroke-width="1.6"><rect x="2" y="5" width="30" height="24"/><path d="M2 5l15 13L32 5"/></svg>
    <h3>EMAIL</h3><p>hello@calmwell.example</p><p class="sm">care@calmwell.example</p>
  </div>
  <div class="abs cbox" style="left:831px">
    <svg width="32" height="32" viewBox="0 0 30 30" fill="none" stroke="var(--teal)" stroke-width="1.6"><circle cx="15" cy="15" r="12"/><path d="M15 8v8l-4 3"/></svg>
    <h3>WORKING HOURS</h3><p>Mon-Sat 09:00-20:00<br>Sunday Emergency only</p>
  </div>
</section>

<footer class="abs footer">
  <div class="fbrand">CALMWELL</div>
  <div class="tag">Leading the Way in Medical<br>Execellence, Trusted Care.</div>
  <div class="fcol" style="left:406px"><h4>Important Links</h4>
    <ul><li>Appointment</li><li>Doctors</li><li>Services</li><li>About Us</li></ul></div>
  <div class="fcol" style="left:560px"><h4>Contact Us</h4>
    <ul><li>Call: (555) 010-2040</li><li>Email: hello@calmwell.example</li><li>Address: 0123 Some place</li><li>Some country</li></ul></div>
  <div class="fcol" style="left:796px"><h4>Newsletter</h4></div>
  <div class="news">Enter your email address
    <svg width="22" height="20" viewBox="0 0 22 20" fill="#1f3b8f"><path d="M1 9L21 1l-6 18-4-7z"/></svg></div>
  <div class="rule"></div>
  <div class="copyright">© 2021 Hospital’s name All Rights Reserved by Northleaf Studio</div>
  <div class="fsocial"><i></i><i></i><i></i></div>
</footer>

</body>
</html>
```